Request for Business Card Design

Hi. My name is Marlene, I am looking for a new business card design for my company, Quarrow Signal Instruments, LLC. I really like the design you did for Tarsel Venture and was hoping you could do something similar using our full logo and our mark. I am also open to any raised texture design using our mark. I have attached our full logo, which would need to be somewhere on the card, as well as the mark in both outline and full form, as well as our brand colors / guide. The card does not have to be white, as long as our logo and mark appear. I actually like darker colored business cards more, but am open to all options. If you are interested in working with me, please let me know. We would also take the business card design into letterhead design if you can do that.

```html
<!DOCTYPE html>
<html lang="en">
<head>
<meta charset="utf-8">
<title>Quarrow Signal Instruments – Business Card</title>
<link href="https://fonts.googleapis.com/css2?family=Open+Sans:wght@400;600;700&display=swap" rel="stylesheet">
<style>
  :root {
    --backdrop: #3a3a3b;
    --card: #1b1b1c;
    --emboss: #262627;
    --brand-blue: #1a9bc9;
    --ink-light: #f2f2f2;
  }
  * { margin: 0; padding: 0; box-sizing: border-box; }
  html, body { width: 1200px; height: 689px; overflow: hidden; }
  body {
    background: var(--backdrop);
    font-family: "Open Sans", Arial, sans-serif;
    position: relative;
  }
  .card {
    position: absolute;
    top: 196px;
    width: 520px;
    height: 297px;
    background: var(--card);
    border-radius: 22px;
  }
  .card--front { left: 60px; }
  .card--back { left: 620px; }

  .wordmark {
    position: absolute;
    display: flex;
    align-items: center;
    gap: 14px;
    font-weight: 700;
    text-transform: uppercase;
    letter-spacing: 1px;
  }
  .wordmark__dot { border-radius: 50%; flex: none; }

  .card--front .wordmark {
    left: 62px; top: 118px;
    color: var(--emboss);
    font-size: 30px;
    line-height: 1.05;
  }
  .card--front .wordmark__dot { width: 58px; height: 58px; background: var(--emboss); }

  .card--back .wordmark {
    left: 34px; top: 132px;
    color: var(--ink-light);
    font-size: 17px;
    line-height: 1.1;
  }
  .card--back .wordmark__dot { width: 38px; height: 38px; background: var(--brand-blue); }

  .divider {
    position: absolute;
    left: 292px; top: 40px;
    width: 2px; height: 217px;
    background: var(--brand-blue);
  }
  .contact {
    position: absolute;
    left: 312px; top: 40px;
    color: var(--ink-light);
    font-size: 12.5px;
    line-height: 1.5;
  }
  .contact__name {
    color: var(--brand-blue);
    font-weight: 700;
    font-size: 19px;
    letter-spacing: 0.5px;
    line-height: 1.2;
  }
  .contact__role { margin-bottom: 18px; }
  .contact__list { list-style: none; margin-bottom: 18px; }
  .contact__list li { display: flex; align-items: center; gap: 8px; }
  .contact__list svg { width: 11px; height: 11px; fill: var(--brand-blue); flex: none; }
</style>
</head>
<body>
  <section class="card card--front" aria-label="Card front">
    <div class="wordmark">
      <span class="wordmark__dot"></span>
      <span>Quarrow Signal<br>Instruments</span>
    </div>
  </section>

  <section class="card card--back" aria-label="Card back">
    <div class="wordmark">
      <span class="wordmark__dot"></span>
      <span>Quarrow Signal<br>Instruments</span>
    </div>
    <div class="divider"></div>
    <div class="contact">
      <p class="contact__name">OWEN BARLOW</p>
      <p class="contact__role">Managing Director</p>
      <ul class="contact__list">
        <li><svg viewBox="0 0 24 24"><path d="M6.6 10.8a15.1 15.1 0 0 0 6.6 6.6l2.2-2.2c.3-.3.7-.4 1-.2 1.1.4 2.3.6 3.6.6.6 0 1 .4 1 1V20c0 .6-.4 1-1 1A17 17 0 0 1 3 4c0-.6.4-1 1-1h3.5c.6 0 1 .4 1 1 0 1.3.2 2.5.6 3.6.1.3 0 .7-.2 1z"/></svg>123 456 789</li>
        <li><svg viewBox="0 0 24 24"><path d="M2 5h20v14H2zm2 2v.5l8 5 8-5V7l-8 5z"/></svg>info@yourgmail.com</li>
        <li><svg viewBox="0 0 24 24"><circle cx="12" cy="12" r="10"/></svg>www.yourwebsite.com</li>
      </ul>
      <p>Your address, City<br>State, Zip 1234</p>
    </div>
  </section>
</body>
</html>
```